Modern, clean business card for Clearbrook Optics

Updated business card with a modern look.

Logo on the front
Dr Tavin R Marquell and Associates on the front.
Three locations on the back:
Ridgefront Brantmart
509-555-0142
18342 E Fernhollow Ave

Pelham Brantmart
509-555-0187
4716 W Dunmore Ave

Copper Bluff Brantmart
509-555-0163
3854 S Kettering Rd

Facebook icon. www.clearbrookoptix.example

Nice open white space on back for writing next appointment time.

Target Market(s)

Main target is female 25-50, but I would like broad appeal.

Industry/Entity Type

Healthcare

Contact Information for Business Card

Modern look

Font styles to use
Serif

Requirements
Must have
• Logo and Dr Tavin R Marquell and Associates on front.
• 3 locations on back
• white space for noting next appointment

```html
<!DOCTYPE html>
<html lang="en">
<head>
<meta charset="utf-8">
<title>Clearbrook Optics – Business Card Front</title>
<link rel="stylesheet" href="https://fonts.googleapis.com/css2?family=Roboto:wght@400;700&display=swap">
<style>
  :root {
    --page-bg: #e6e7e9;
    --card-white: #ffffff;
    --brand-blue: #1a8fd0;
    --brand-navy: #2f3f7a;
    --charcoal: #3a3b3d;
    --band-text: #ffffff;
  }
  * { margin: 0; padding: 0; box-sizing: border-box; }
  html, body {
    width: 1200px;
    height: 900px;
    overflow: hidden;
    background: var(--page-bg);
    font-family: "Roboto", Arial, sans-serif;
  }
  .card {
    position: absolute;
    left: 75px;
    top: 150px;
    width: 1050px;
    height: 600px;
    background: var(--card-white);
    box-shadow: 0 6px 24px rgba(0,0,0,0.18);
    overflow: hidden;
  }
  .card-shapes {
    position: absolute;
    inset: 0;
  }
  .band-blue { fill: var(--brand-blue); }
  .block-charcoal { fill: var(--charcoal); }
  .practice-name {
    position: absolute;
    left: 0;
    top: 95px;
    width: 650px;
    height: 62px;
    line-height: 62px;
    padding-right: 24px;
    text-align: right;
    white-space: nowrap;
    color: var(--band-text);
    font-size: 26px;
    font-weight: 400;
  }
  .brand {
    position: absolute;
    left: 0;
    right: 0;
    top: 270px;
    text-align: center;
  }
  .brand-line {
    display: inline-flex;
    align-items: center;
    gap: 18px;
    white-space: nowrap;
  }
  .brand-dot {
    width: 46px;
    height: 46px;
    border-radius: 50%;
    background: var(--brand-blue);
  }
  .brand-name {
    color: var(--brand-navy);
    font-size: 64px;
    font-weight: 700;
    letter-spacing: 1px;
    text-transform: uppercase;
  }
  .brand-tagline {
    margin-top: 6px;
    color: var(--brand-navy);
    font-size: 30px;
    font-weight: 700;
    letter-spacing: 2px;
    text-transform: uppercase;
    white-space: nowrap;
  }
</style>
</head>
<body>
  <div class="card">
    <svg class="card-shapes" width="1050" height="600" viewBox="0 0 1050 600" aria-hidden="true">
      <polygon class="block-charcoal" points="790,0 1050,0 1050,195 735,195"/>
      <polygon class="band-blue" points="0,95 690,95 668,157 0,157"/>
      <polygon class="block-charcoal" points="800,470 1050,470 1050,548 775,548"/>
      <polygon class="band-blue" points="0,548 760,548 740,600 0,600"/>
    </svg>

    <div class="practice-name">Dr Tavin R Marquell and Associates</div>

    <div class="brand">
      <div class="brand-line">
        <span class="brand-dot"></span>
        <span class="brand-name">Clearbrook Optics</span>
      </div>
      <div class="brand-tagline">Advanced Eye Care</div>
    </div>
  </div>
</body>
</html>
```